Redesign of luchtvoorraadpunt.nl – Clean, Trustworthy & User-Friendly Medical Equipment We...

PLEASE DO NOT CONTACT US OUTSIDE KRAVELPOINT.COM

We are looking for a talented and creative web designer to redesign the website www.luchtvoorraadpunt.nl, a Dutch online store specializing in medical oxygen concentrators and related products.

The current website is functional but outdated in terms of design, structure, and user experience. We want a fresh, modern, and trustworthy design that reflects the medical and professional nature of the business, while also being clear, accessible, and easy to navigate for a broad audience — including elderly users and people with limited technical skills.

About the Business:
Luchtvoorraadpunt.nl provides high-quality oxygen concentrators and accessories for both home and mobile use. The target audience includes individuals with respiratory conditions, healthcare professionals, and caregivers. Trust, clarity, and ease of use are key.

What We’re Looking For:
A clean and modern layout with a medical/professional feel
Strong focus on usability and accessibility
A design that works flawlessly on desktop and mobile (responsive)
Clear product presentation and easy-to-use navigation
Use of calming colors (e.g. white, light blue, grey tones) that reflect a medical/healthcare environment
Clear call-to-actions (e.g. “Vraag een offerte aan”, “Neem contact op”, etc.)
A design that builds trust and encourages inquiries or purchases

Pages We Need Designed:
Homepage
Product overview page (category)
Product detail page

Inspiration / Style Examples:
We’re looking for something in the style of:

Varnoth Healthcare
Bralto.nl
Welzijnsdepot.nl
Quenby (for clean layout and spacing)

Deliverables:
Full desktop and mobile designs (Figma, Adobe PS)
All source files and assets used (fonts, icons, images, etc.)
Clean and organized layers
Design must be ready for implementation by our development team

Target Market(s)

Luchtvoorraadpunt.nl targets both B2C and B2B audiences within the medical and healthcare sector in europe

Industry/Entity Type

Medical

Number of Pages Required

2 page

Font styles to use
Sans Serif

Requirements
Must have
• Clean and professional design, responsive layout (desktop and mobile), calming medical color scheme (e.g. light blue, white, grey), clear product presentation with specs and images, strong call-to-actions (e.g. "Vraag een offerte aan"), trust elements (certifications, reviews, support info), easy navigation for elderly and non-tech-savvy users, contact form easily accessible, SEO-friendly structure, fast loading design, privacy and regulatory compliance elements (e.g. CE mark info, medical disclaimers).
Should not have
• Overly complex design, dark or aggressive color schemes, small or hard-to-read fonts, cluttered layout, distracting animations, unnecessary pop-ups, autoplay videos or sounds, technical jargon without explanation, hidden contact options, slow-loading pages.

```html
<!DOCTYPE html>
<html lang="en">
<head>
<meta charset="utf-8">
<title>luvo – Oxygen Concentrators</title>
<link href="https://fonts.googleapis.com/css2?family=Outfit:wght@300;400;500;600;700&display=swap" rel="stylesheet">
<style>
:root{
  --blue:#1c4fd8;
  --ink:#1d1d24;
  --muted:#55585f;
  --topbar:#f5f6f8;
  --lightblue:#e8f2fc;
  --card-blue:#eaf3fb;
  --card-grey:#f3f3f4;
  --band-grey:#efeff1;
  --footer:#333336;
  --line:#e3e5e8;
  --white:#fff;
}
*{box-sizing:border-box;margin:0;padding:0}
html,body{width:1200px;height:3405px;overflow:hidden}
body{font-family:'Outfit',sans-serif;color:var(--ink);background:var(--white);position:relative}
a{color:inherit;text-decoration:none}
.abs{position:absolute}
.icon{width:18px;height:18px;stroke:currentColor;fill:none;stroke-width:1.6}

.topbar{position:absolute;top:0;left:0;width:1200px;height:41px;background:var(--topbar);font-size:13px;font-weight:500;text-transform:uppercase;letter-spacing:.2px}
.topbar .group{position:absolute;top:0;height:41px;display:flex;align-items:center;gap:24px}
.topbar .item{display:flex;align-items:center;gap:8px}

.header{position:absolute;top:41px;left:0;width:1200px;height:71px;background:var(--blue)}
.brand{position:absolute;left:141px;top:10px;font-size:48px;font-weight:700;color:var(--white);letter-spacing:-1px;line-height:50px}
.menu-btn{position:absolute;left:298px;top:26px}
.search{position:absolute;left:352px;top:12px;width:478px;height:42px;border-radius:21px;background:#fff;display:flex;align-items:center;padding:0 6px 0 20px;font-size:13px;color:#444}
.search .go{margin-left:auto;width:32px;height:32px;border-radius:50%;background:var(--blue);display:flex;align-items:center;justify-content:center;color:#fff}
.header-tools{position:absolute;left:898px;top:24px;display:flex;align-items:center;gap:26px;color:#fff;font-size:14px}

.nav{position:absolute;top:112px;left:0;width:1200px;height:57px;border-bottom:1px solid var(--line);display:flex;align-items:center;padding-left:143px;font-size:12.5px;font-weight:500;text-transform:uppercase;gap:35px}
.nav .phone{position:absolute;left:904px;display:flex;align-items:center;gap:8px;font-size:15px;text-transform:none}
.nav .phone svg{color:var(--blue)}

.hero{position:absolute;top:170px;left:0;width:1200px;height:517px;border-bottom:4px solid var(--blue);
  background:
   radial-gradient(ellipse 260px 170px at 540px 90px,rgba(92,70,52,.55),transparent 70%),
   radial-gradient(ellipse 220px 260px at 1120px 200px,rgba(250,250,247,.85),transparent 70%),
   radial-gradient(ellipse 200px 230px at 380px 270px,rgba(120,135,160,.55),transparent 70%),
   radial-gradient(ellipse 300px 120px at 560px 330px,rgba(150,110,70,.45),transparent 70%),
   linear-gradient(180deg,#d3cec4 0%,#cbc4b7 60%,#a9a193 78%,#b9b2a5 100%);}
.hero-panel{position:absolute;left:642px;top:115px;width:415px;height:286px;background:rgba(20,20,22,.78);padding:50px 20px 0 51px;color:#fff}
.hero-panel h1{font-size:33px;font-weight:700;line-height:36px}
.hero-panel h2{font-size:25px;font-weight:500;line-height:34px;white-space:nowrap}
.hero-panel p{font-size:15px;line-height:23px;margin-top:6px;font-weight:300;width:320px}
.btn{display:inline-flex;align-items:center;justify-content:center;background:var(--blue);color:#fff;font-size:12px;font-weight:500;text-transform:uppercase;border-radius:24px}
.hero-panel .btn{margin-top:16px;width:138px;height:46px}

.features{position:absolute;top:690px;left:0;width:1200px;height:156px;background:var(--lightblue)}
.feature{position:absolute;top:50px;display:flex;gap:18px;align-items:center}
.feature .circle{width:56px;height:56px;border-radius:50%;background:var(--blue);display:flex;align-items:center;justify-content:center;color:#fff}
.feature b{display:block;font-size:17px;font-weight:500}
.feature span{font-size:14px;color:var(--muted);display:block;margin-top:6px}

.section-title{position:absolute;left:0;width:1200px;text-align:center;font-size:31px;font-weight:500;text-transform:uppercase}

.cat{position:absolute;border-radius:6px;overflow:hidden;padding:30px 16px}
.cat h3{font-size:17px;font-weight:400;line-height:21px;position:relative;z-index:1}
.cat .more{position:absolute;left:16px;bottom:34px;font-size:12px;font-weight:500;color:var(--blue);text-transform:uppercase;z-index:1}
.cat .photo{position:absolute;border-radius:8px}
.cat .blob{position:absolute;border-radius:50%}

.about p{position:absolute;left:205px;top:1456px;width:790px;text-align:center;font-size:13.5px;line-height:24px;color:#333}

.brand-band{position:absolute;top:1686px;left:0;width:1200px;height:438px;background:var(--band-grey)}
.brand-card{position:absolute;top:144px;width:214px;height:142px;background:#fff;border-radius:4px;display:flex;align-items:center;justify-content:center;font-size:38px;font-weight:400;color:#2a57a8}
.slider-line{position:absolute;top:332px;height:1px;background:#d5d6da}
.arrow{position:absolute;width:28px;height:28px;border-radius:50%;display:flex;align-items:center;justify-content:center;color:#fff}

.tabs{position:absolute;top:2210px;left:0;width:1200px;font-size:15px;text-transform:uppercase}
.tabs .t{position:absolute;top:0}
.tabs .rule{position:absolute;left:141px;top:39px;width:916px;height:1px;background:var(--line)}
.tabs .active-rule{position:absolute;left:628px;top:37px;width:107px;height:3px;background:var(--ink)}

.product{position:absolute;top:2288px;width:213px;height:379px;border-radius:6px;text-align:center;padding-top:26px}
.product h4{font-size:16px;font-weight:500;line-height:22px;padding:0 12px;white-space:nowrap}
.product .disc{position:absolute;left:32px;top:82px;width:150px;height:150px;border-radius:50%}
.product .shot{position:absolute;border-radius:10px}
.product .price{position:absolute;left:0;top:268px;width:100%;font-size:16px}
.product .price s{color:#888;font-size:13px;margin-right:8px}
.product .btn{position:absolute;left:48px;top:306px;width:117px;height:40px;font-size:11px}

.feat2{position:absolute;top:2733px;width:234px;text-align:center}
.feat2 .circle{width:62px;height:62px;border-radius:50%;background:#dfe8fb;margin:0 auto 12px;display:flex;align-items:center;justify-content:center;color:var(--blue)}
.feat2 b{display:block;font-size:15px;font-weight:500}
.feat2 span{font-size:12.5px;color:var(--muted)}
.feat-div{position:absolute;top:2745px;width:1px;height:85px;background:var(--line)}

.newsletter{position:absolute;top:2886px;left:0;width:1200px;height:122px;background:var(--blue);color:#fff}
.newsletter h3{position:absolute;left:143px;top:32px;font-size:24px;font-weight:700;text-transform:uppercase}
.newsletter p{position:absolute;left:143px;top:64px;font-size:14px}
.nl-form{position:absolute;left:670px;top:40px;width:388px;height:42px;border-radius:21px;background:#fff;display:flex;align-items:center;padding:0 4px 0 20px;font-size:11px;color:#444}
.nl-form .btn{margin-left:auto;width:82px;height:34px;font-size:11px}

.footer{position:absolute;top:3008px;left:0;width:1200px;height:397px;background:var(--footer);color:#fff}
.col{position:absolute;top:67px}
.col h5{font-size:18px;font-weight:500;text-transform:uppercase}
.col h5:after{content:"";display:block;width:32px;height:2px;background:#fff;margin-top:8px}
.col ul{list-style:none;margin-top:18px}
.col li{font-size:12.5px;line-height:29px}
.col li:before{content:"• ";font-size:9px}
.footer-brand{position:absolute;left:910px;top:116px;font-size:52px;font-weight:700;letter-spacing:-1px}
.pay{position:absolute;left:722px;top:194px;width:335px;height:83px;background:#fff;border-radius:8px;color:var(--ink);padding:12px 14px}
.pay .head{display:flex;align-items:center;gap:6px;font-size:15px}
.pay .head b{font-weight:700;font-size:17px}
.pay .cards{display:flex;gap:20px;margin-top:12px;font-size:16px;font-weight:700;color:#1f3a8f}
.foot-line{position:absolute;left:143px;top:345px;width:914px;height:1px;background:#555}
.copy{position:absolute;left:143px;top:362px;font-size:12px}
.follow{position:absolute;left:965px;top:358px;display:flex;align-items:center;gap:8px;font-size:12px}
.follow .sq{width:26px;height:26px;border-radius:50%;border:1px solid #fff}
</style>
</head>
<body>

<div class="topbar">
  <div class="group" style="left:140px">
    <a class="item" href="#"><svg class="icon" viewBox="0 0 24 24"><path d="M3 11l9-7 9 7v9H3z"/></svg>Home</a>
    <a class="item" href="#"><svg class="icon" viewBox="0 0 24 24"><circle cx="12" cy="12" r="9"/><path d="M12 8v8"/></svg>About Us</a>
    <a class="item" href="#"><svg class="icon" viewBox="0 0 24 24"><path d="M4 5h12v9H8l-4 3z M16 9h4v9l-3-2h-7"/></svg>Contact</a>
  </div>
  <div class="group" style="left:666px">
    <a class="item" href="#"><svg class="icon" viewBox="0 0 24 24"><rect x="4" y="6" width="16" height="14" rx="2"/><path d="M8 6V4h8v2"/></svg>Delivery</a>
    <a class="item" href="#"><svg class="icon" viewBox="0 0 24 24"><path d="M12 3l8 4v10l-8 4-8-4V7z M4 7l8 4 8-4 M12 11v10"/></svg>Stock</a>
    <a class="item" href="#"><svg class="icon" viewBox="0 0 24 24"><circle cx="12" cy="8" r="4"/><path d="M4 21c1-5 15-5 16 0"/></svg>Login</a>
    <a class="item" href="#"><svg class="icon" viewBox="0 0 24 24"><circle cx="12" cy="12" r="9"/><circle cx="12" cy="10" r="3"/><path d="M6 18c2-3 10-3 12 0"/></svg>Register</a>
  </div>
</div>

<header class="header">
  <div class="brand">luvo</div>
  <svg class="menu-btn" width="22" height="18" viewBox="0 0 22 18" stroke="#fff" stroke-width="2"><path d="M1 3h20M1 9h20M1 15h20"/></svg>
  <div class="search">Search here...<span class="go"><svg class="icon" style="width:15px;height:15px" viewBox="0 0 24 24"><circle cx="11" cy="11" r="7"/><path d="M16 16l5 5"/></svg></span></div>
  <div class="header-tools">
    <svg class="icon" style="width:22px;height:22px" viewBox="0 0 24 24"><path d="M4 10h14l-4-4 M20 14H6l4 4"/></svg>
    <svg class="icon" style="width:20px;height:20px" viewBox="0 0 24 24"><path d="M12 20s-8-5-8-11a4 4 0 018-1 4 4 0 018 1c0 6-8 11-8 11z"/></svg>
    <span style="display:flex;align-items:center;gap:8px"><svg class="icon" style="width:20px;height:20px" viewBox="0 0 24 24"><path d="M5 8h14l-1 12H6z M9 8V6a3 3 0 016 0v2"/></svg>€0.00</span>
  </div>
</header>

<nav class="nav">
  <a href="#">Oxygen Concentrator ⌄</a>
  <a href="#">Portable Oxygen Concentrator ⌄</a>
  <a href="#">Filters</a>
  <a href="#">Rental</a>
  <a href="#">Supplies</a>
  <span class="phone"><svg class="icon" style="width:22px;height:22px" viewBox="0 0 24 24"><path d="M5 3l4 1 1 5-2 1a12 12 0 006 6l1-2 5 1 1 4c-9 1-17-7-16-16z"/></svg>0031-701234567</span>
</nav>

<section class="hero" role="img" aria-label="Older man seated in an armchair in a bright living room with bookshelves, holding a portable oxygen concentrator">
  <div class="hero-panel">
    <h1>NIMBUS 5</h1>
    <h2>OXYGEN CONCENTRATOR</h2>
    <p>Duis autem vel eum iriure dolor in hendrerit in vulputate velit esse molestie.</p>
    <a class="btn" href="#">Shop Now</a>
  </div>
</section>

<section class="features">
  <div class="feature" style="left:70px"><div class="circle"><svg class="icon" style="width:28px;height:28px" viewBox="0 0 24 24"><path d="M2 7h12v9H2z M14 10h4l3 3v3h-7"/><circle cx="6" cy="17" r="2"/><circle cx="17" cy="17" r="2"/></svg></div><div><b>Free Shipping</b><span>Above € 250 in the EU</span></div></div>
  <div class="feature" style="left:325px"><div class="circle"><svg class="icon" style="width:28px;height:28px" viewBox="0 0 24 24"><rect x="7" y="3" width="10" height="18" rx="2"/><circle cx="12" cy="12" r="3"/></svg></div><div><b>Oxygen Concentrator</b><span>Oxygen concentrator for travel</span></div></div>
  <div class="feature" style="left:636px"><div class="circle"><svg class="icon" style="width:28px;height:28px" viewBox="0 0 24 24"><path d="M3 5h3l2 10h10l2-7H7"/><circle cx="10" cy="19" r="1.5"/><circle cx="17" cy="19" r="1.5"/></svg></div><div><b>Secure Shopping</b><span>Best security features</span></div></div>
  <div class="feature" style="left:888px"><div class="circle"><svg class="icon" style="width:28px;height:28px" viewBox="0 0 24 24"><circle cx="12" cy="12" r="8"/><path d="M12 8l1.2 2.6 2.8.3-2 2 .6 2.8-2.6-1.4-2.6 1.4.6-2.8-2-2 2.8-.3z"/></svg></div><div><b>22 Years Experience</b><span>In the Industry</span></div></div>
</section>

<h2 class="section-title" style="top:902px">Shop by Categories</h2>

<div class="cat" style="left:141px;top:965px;width:291px;height:162px;background:var(--card-blue)">
  <div class="blob" style="left:158px;top:-30px;width:170px;height:200px;background:#d7e7f7"></div>
  <div class="photo" role="img" aria-label="White and blue quiet oxygen concentrator" style="left:175px;top:10px;width:80px;height:142px;background:linear-gradient(90deg,#f6f8fb 40%,#3f7bd6 41%,#5c92e0)"></div>
  <h3>Halvik 4.0<br>Quiet Oxygen<br>Concentrator</h3>
  <a class="more" href="#">Shop Now ●</a>
</div>
<div class="cat" style="left:455px;top:965px;width:291px;height:162px;background:var(--card-grey)">
  <div class="blob" style="left:165px;top:-20px;width:150px;height:190px;background:#e9e7e6"></div>
  <div class="photo" role="img" aria-label="Light blue home oxygen concentrator" style="left:175px;top:12px;width:80px;height:140px;background:linear-gradient(180deg,#f2f6f9,#bfd3e3)"></div>
  <h3>Clearwave Oxygen<br>Concentrator</h3>
  <a class="more" href="#">Shop Now ●</a>
</div>
<div class="cat" style="left:768px;top:965px;width:291px;height:162px;background:var(--card-grey)">
  <div class="blob" style="left:170px;top:-20px;width:150px;height:190px;background:#e7e8ec"></div>
  <div class="photo" role="img" aria-label="Black continuous flow refill station" style="left:160px;top:14px;width:100px;height:138px;background:linear-gradient(180deg,#3a3b3f,#141416)"></div>
  <h3>Refilo Station<br>Continuous<br>Flow</h3>
  <a class="more" href="#">Shop Now ●</a>
</div>
<div class="cat" style="left:141px;top:1146px;width:448px;height:162px;background:var(--card-grey)">
  <div class="photo" role="img" aria-label="Nasal cannula tubing and oxygen mask on a mannequin head" style="left:160px;top:8px;width:280px;height:150px;background:linear-gradient(90deg,#eceef0,#d5dadd 60%,#b8c4c6)"></div>
  <h3>Cannulas And<br>Masks</h3>
  <a class="more" href="#">Shop Now ●</a>
</div>
<div class="cat" style="left:610px;top:1146px;width:448px;height:162px;background:var(--card-blue)">
  <div class="blob" style="left:318px;top:-30px;width:180px;height:210px;background:#d4e6f4"></div>
  <div class="photo" role="img" aria-label="Black compact oxygen concentrator" style="left:305px;top:10px;width:95px;height:145px;background:linear-gradient(180deg,#45464a,#18181a)"></div>
  <h3>Oxygen Concentrator<br>Compact</h3>
  <a class="more" href="#">Shop Now ●</a>
</div>

<section class="about">
  <h2 class="section-title" style="top:1398px">LUVO BV Oxygen Concentrator</h2>
  <p>LUVO BV was founded in 2003 and has a premium range of oxygen concentrators. We have the largest online offers for the Netherlands and Belgium.Whether you are looking for a fixed oxygen concentrator or a portable / portable / mobile oxygen concentrator. We make the difference in knowledge, service and low prices.</p>
  <a class="btn abs" href="#" style="left:509px;top:1549px;width:182px;height:45px;font-size:12.5px">Request a Quote</a>
</section>

<section class="brand-band">
  <h2 class="section-title" style="top:84px">Shop by Brand</h2>
  <div class="brand-card" style="left:141px;letter-spacing:2px">AIRVEN</div>
  <div class="brand-card" style="left:375px">Tolvane</div>
  <div class="brand-card" style="left:609px">Halvik</div>
  <div class="brand-card" style="left:843px">Brisola</div>
  <div class="slider-line" style="left:141px;width:415px"></div>
  <div class="slider-line" style="left:643px;width:414px"></div>
  <div class="arrow" style="left:567px;top:318px;background:#8f9095">‹</div>
  <div class="arrow" style="left:604px;top:318px;background:var(--blue)">›</div>
</section>

<div class="tabs">
  <span class="t" style="left:436px;color:#666">Recently Viewed</span>
  <span class="t" style="left:628px;font-weight:500">Most Viewed</span>
  <div class="rule"></div>
  <div class="active-rule"></div>
</div>

<div class="arrow" style="left:99px;top:2466px;background:#8f9095">‹</div>
<div class="arrow" style="left:1077px;top:2466px;background:var(--blue)">›</div>

<div class="product" style="left:141px;background:var(--card-blue)">
  <h4>Varnoth Respira<br>Clearwave oxygen...</h4>
  <div class="disc" style="background:#d4e5f5"></div>
  <div class="shot" role="img" aria-label="Light blue home oxygen concentrator" style="left:60px;top:84px;width:94px;height:150px;background:linear-gradient(180deg,#8fbcec,#4d8bd8 60%,#3b76c4)"></div>
  <div class="price"><s>€900.00</s>€790.25</div>
  <a class="btn" href="#">Shop Now</a>
</div>
<div class="product" style="left:375px;background:var(--card-grey)">
  <h4>Firesafe valve</h4>
  <div class="disc" style="background:#f3e8ea"></div>
  <div class="shot" role="img" aria-label="Clear plastic inline firesafe valve" style="left:92px;top:92px;width:30px;height:130px;border-radius:14px;background:linear-gradient(90deg,#dfe4dc,#f7f8f4,#cfd6cb)"></div>
  <div class="price">€9.95</div>
  <a class="btn" href="#">Shop Now</a>
</div>
<div class="product" style="left:609px;background:var(--card-blue)">
  <h4>Oxygen Concentrator<br>Compact 520DX</h4>
  <div class="disc" style="background:#c9def0"></div>
  <div class="shot" role="img" aria-label="Black compact oxygen concentrator" style="left:64px;top:84px;width:86px;height:150px;background:linear-gradient(180deg,#4a4b4f,#1a1a1c)"></div>
  <div class="price"><s>€899.25</s>€801.15</div>
  <a class="btn" href="#">Shop Now</a>
</div>
<div class="product" style="left:843px;background:var(--card-grey)">
  <h4>Oxygen Mask With<br>2.1 Meter Hose</h4>
  <div class="disc" style="background:#f1e6e8"></div>
  <div class="shot" role="img" aria-label="Green oxygen mask with hose on a mannequin head" style="left:52px;top:90px;width:110px;height:140px;border-radius:40px 40px 12px 12px;background:linear-gradient(180deg,#e6e8e9,#c4cacb 55%,#a9ccbf)"></div>
  <div class="price"><s>€2.73</s>€2.18</div>
  <a class="btn" href="#">Shop Now</a>
</div>

<div class="feat2" style="left:131px"><div class="circle"><svg class="icon" style="width:28px;height:28px" viewBox="0 0 24 24"><path d="M2 7h12v9H2z M14 10h4l3 3v3h-7"/><circle cx="6" cy="17" r="2"/><circle cx="17" cy="17" r="2"/></svg></div><b>Free Shipping</b><span>Above € 250 in the EU</span></div>
<div class="feat-div" style="left:364px"></div>
<div class="feat2" style="left:365px"><div class="circle"><svg class="icon" style="width:26px;height:26px" viewBox="0 0 24 24"><path d="M12 20s-8-5-8-11a4 4 0 018-1 4 4 0 018 1c0 6-8 11-8 11z"/></svg></div><b>Oxygen Concentrator</b><span>Oxygen Concentrator For Travel</span></div>
<div class="feat-div" style="left:599px"></div>
<div class="feat2" style="left:599px"><div class="circle"><svg class="icon" style="width:26px;height:26px" viewBox="0 0 24 24"><path d="M12 3l8 3v6c0 5-4 8-8 9-4-1-8-4-8-9V6z M8.5 12l2.5 2.5 4.5-5"/></svg></div><b>Secure Shopping</b><span>Best Security Features</span></div>
<div class="feat-div" style="left:833px"></div>
<div class="feat2" style="left:834px"><div class="circle"><svg class="icon" style="width:26px;height:26px" viewBox="0 0 24 24"><circle cx="12" cy="6" r="2.5"/><path d="M7 20l1.5-4 3.5-1 3.5 1 1.5 4 M3 20h18"/></svg></div><b>22 Years</b><span>Experience</span></div>

<section class="newsletter">
  <h3>Sign up to Newsletter</h3>
  <p>Subscribe to get the latest deals, promotions and offering.</p>
  <div class="nl-form">Enter your email address<a class="btn" href="#">Sign Up</a></div>
</section>

<footer class="footer">
  <div class="col" style="left:143px"><h5>About Us</h5><ul><li>About Us</li><li>Delivery</li><li>Privacy Policy</li><li>Terms &amp; Conditions</li><li>Business</li><li>Frequently asked questions</li></ul></div>
  <div class="col" style="left:425px"><h5>Customer Service</h5><ul><li>Contact</li><li>Warranty and Service</li><li>Returns</li><li>Site Map</li><li>Brands</li></ul></div>
  <div class="col" style="left:721px"><h5>My Account</h5><ul><li>My Account</li><li>Order History</li></ul></div>
  <div class="footer-brand">luvo</div>
  <div class="pay">
    <div class="head"><svg width="13" height="15" viewBox="0 0 13 15"><rect x="1" y="6" width="11" height="8" rx="1" fill="#1d1d24"/><path d="M3.5 6V4a3 3 0 016 0v2" stroke="#1d1d24" stroke-width="1.6" fill="none"/></svg>Secure payments powered by <b>Payvora</b></div>
    <div class="cards"><span>Cardo</span><span>Velpay</span><span>Amora</span><span>Ideo</span><span>Paylen</span></div>
  </div>
  <div class="foot-line"></div>
  <div class="copy">© 2025, LUVO BV. All Rights Reserved</div>
  <div class="follow">Follow Us: <span class="sq"></span></div>
</footer>

</body>
</html>
```